Lantern Petals Website v.1 - attract floral shop franchisees

I need a simple information website for my new business. We are a franchisor of flower shops. The overall purpose of the website is to promote the company and the service, especially to potential franchisees and retailers. Only about 4 pages are required including homepage, About, For Supermarkets, For Franchisees, and Contact. No special functions are required except the site will have two separate inquiry forms that must be filled out online and submitted via automated email. Similarly, an email form should be linked from the Contact page. I have a logo and business cards designed by ArtMingle, and I would like the site to have a consistent color scheme and style. The key to design will be to express the joy and love associated with flowers and floral bouquets.
IMPORTANT - I will be exporting the website design to Wordpress CMS in a site hosted by HostNimbus. For smooth integration into WordPress hosted by HostNimbus, the designer should build the site using a WordPress-friendly format. Ideally, they should use HTML, CSS, and PHP. Creating a custom theme or using a page builder that exports to WordPress-compatible files is best. This ensures the site can be easily imported and managed within WordPress.

Target Market(s)

Potential franchisees (existing florists or creative types who might like to own a floral business) and supermarkets who might want us to run their floral department

Industry/Entity Type

Floral retailing

Requirements
Must have
• A brand theme that is beautiful, consistent throughout and builds on the logo design
Nice to have
• Show gender and ethnic diversity in customers and florists. Pictures of happy florists (for franchisees) and pictures of amazing floral department displays (for supermarkets)

```html
<!DOCTYPE html>
<html lang="en">
<head>
<meta charset="utf-8">
<title>Lantern Petals – Flower Shop Franchises</title>
<link href="https://fonts.googleapis.com/css2?family=Montserrat:wght@500;700&family=Poppins:wght@400;500;600&family=Oswald:wght@600&family=Great+Vibes&display=swap" rel="stylesheet">
<style>
:root{
  --green:#0f8a2e;
  --green-bright:#22c43a;
  --orange:#f39a0c;
  --ink:#1d1d1d;
  --text:#3a3a3a;
  --dark:#141414;
  --white:#ffffff;
  --ornament:#cfe6cf;
}
*{margin:0;padding:0;box-sizing:border-box}
html,body{width:1200px;height:4549px;overflow:hidden}
body{font-family:"Poppins",sans-serif;color:var(--text);background:var(--white);position:relative}
.abs{position:absolute}
.img-fill{position:absolute}
.site-header{position:absolute;top:0;left:0;width:1200px;height:99px;background:var(--white)}
.brand{position:absolute;display:flex;align-items:center;gap:10px}
.brand-dot{width:30px;height:30px;border-radius:50%;background:var(--orange)}
.brand-name{font-family:"Montserrat",sans-serif;font-weight:700;font-size:24px;color:var(--green);letter-spacing:.5px}
.header-brand{left:141px;top:32px}
.contact-chip{position:absolute;top:32px;display:flex;align-items:center;gap:12px;font-size:14px;color:var(--ink)}
.chip-icon{width:32px;height:32px;border-radius:50%;background:var(--orange);display:flex;align-items:center;justify-content:center}
.main-nav{position:absolute;top:99px;left:0;width:1200px;height:42px;background:var(--green);display:flex;align-items:center;justify-content:space-between;padding:0 140px;font-size:12.5px;color:var(--white)}
.main-nav a{color:var(--white);text-decoration:none}
.main-nav a.active{font-weight:600}
.main-nav .sep{opacity:.8}
.hero{position:absolute;top:141px;left:0;width:1200px;height:530px;background:linear-gradient(100deg,#6b5a4a 0%,#a88d6e 30%,#d9b08a 50%,#8a7357 75%,#4f5a3c 100%)}
.hero-shade{position:absolute;inset:0;background:linear-gradient(180deg,rgba(0,0,0,0) 40%,rgba(0,0,0,.35) 100%)}
.hero-title{position:absolute;top:300px;left:0;width:1200px;text-align:center;font-family:"Oswald",sans-serif;font-weight:600;font-size:47px;line-height:62px;color:var(--white);text-shadow:0 2px 6px rgba(0,0,0,.4)}
.btn{display:inline-flex;align-items:center;justify-content:center;background:var(--orange);color:var(--white);border-radius:22px;font-size:12px;text-decoration:none}
.hero-btn{position:absolute;left:529px;top:440px;width:142px;height:40px;font-size:13px}
.btn-franchise{position:absolute;height:38px;width:142px;padding-right:34px;border-radius:20px}
.btn-franchise::after{content:"";position:absolute;right:6px;top:6px;width:26px;height:26px;border-radius:50%;background:var(--white)}
.sec-head{position:absolute;display:flex;align-items:baseline;gap:8px}
.sec-head .lead{font-family:"Montserrat",sans-serif;font-weight:700;font-size:34px;color:var(--ink)}
.sec-head .script{font-family:"Great Vibes",cursive;font-size:58px;color:var(--ink);line-height:1}
.ornament{position:absolute;width:36px;height:74px;border-radius:18px;background:var(--ornament);opacity:.6}
.about{position:absolute;top:671px;left:0;width:1200px;height:603px;background:linear-gradient(90deg,#f7f2ea 0%,#eef5ec 50%,#d3ecd7 100%)}
.photo-frame{position:absolute;background:var(--white);border-radius:18px;box-shadow:0 4px 14px rgba(0,0,0,.12);padding:10px}
.photo-frame .ph{width:100%;height:100%;border-radius:12px}
.badge{position:absolute;width:122px;height:122px;border-radius:50%;background:#d8cfc3;border:8px solid var(--white)}
.about-copy{position:absolute;left:600px;top:183px;width:455px;font-size:11.8px;line-height:20px;color:var(--ink)}
.about-copy p+p{margin-top:17px}
.opportunity{position:absolute;top:1274px;left:0;width:1200px;height:768px;background:linear-gradient(180deg,#fbfbfb 0%,#f6f0ee 60%,#fafafa 100%)}
.card{position:absolute;top:217px;width:283px;height:357px;background:var(--white);border-radius:18px;padding:10px;box-shadow:0 4px 14px rgba(0,0,0,.1)}
.card .ph{width:100%;height:100%;border-radius:12px;position:relative}
.card-label{position:absolute;left:0;right:0;top:212px;text-align:center;font-family:"Montserrat",sans-serif;font-weight:700;font-size:20px;line-height:26px;color:var(--white);text-shadow:0 1px 4px rgba(0,0,0,.5)}
.card-arrow{position:absolute;left:50%;margin-left:-13px;top:293px;width:26px;height:26px;background:var(--orange);border-radius:4px;display:flex;align-items:center;justify-content:center}
.why{position:absolute;top:2042px;left:0;width:1200px;height:606px;background:linear-gradient(90deg,#e2f0e0 0%,#eef3e6 45%,#c9b9a4 65%,#b6a38e 100%)}
.why-list{position:absolute;left:141px;top:188px;list-style:none;font-size:11.5px;color:var(--ink)}
.why-list li{height:28.2px;display:flex;align-items:center;gap:10px}
.tick{width:15px;height:15px}
.growth{position:absolute;top:2648px;left:0;width:1200px;height:577px;background:var(--white)}
.growth-text{position:absolute;left:270px;top:176px;width:660px;text-align:center;font-size:11.5px;line-height:20px;color:var(--ink)}
.faq{position:absolute;top:3225px;left:0;width:1200px;height:649px;background:linear-gradient(90deg,#f5ead6 0%,#eef0dd 50%,#cfe8d2 100%)}
.faq-item{position:absolute;left:286px;width:628px;background:var(--white);border-radius:4px;display:flex;align-items:center;justify-content:space-between;padding:0 22px;font-size:12.5px;color:var(--ink);letter-spacing:.4px}
.faq-item .toggle{font-size:20px;font-weight:500}
.faq-open{position:absolute;left:286px;top:181px;width:628px;height:142px;background:var(--white);border-radius:4px;border-bottom:5px solid var(--green);padding:16px 22px}
.faq-open .q{display:flex;justify-content:space-between;font-size:12px;font-weight:600;color:var(--ink)}
.faq-open .a{margin-top:24px;font-size:11.5px;line-height:23px;text-align:justify;color:#555;letter-spacing:.3px}
.contact-bg{position:absolute;top:3874px;left:0;width:1200px;height:355px;background:#f3f3f3;overflow:hidden}
.contact-word{position:absolute;left:70px;top:20px;font-family:"Montserrat",sans-serif;font-weight:700;font-size:200px;letter-spacing:6px;color:rgba(0,0,0,.04)}
.footer{position:absolute;top:4229px;left:0;width:1200px;height:271px;background:var(--dark)}
.contact-card{position:absolute;top:4024px;left:176px;width:848px;height:346px;display:flex;box-shadow:0 6px 20px rgba(0,0,0,.15)}
.form-pane{width:495px;background:var(--white);position:relative}
.details-pane{flex:1;background:linear-gradient(135deg,#f6ead0 0%,#e8efd8 60%,#d4ecd6 100%);position:relative}
.pane-title{position:absolute;font-family:"Montserrat",sans-serif;font-weight:700;font-size:27px;color:var(--ink)}
.field{position:absolute;height:35px;border:1px solid #ddd;font-size:11px;color:#666;padding:9px 8px}
.detail{position:absolute;left:34px;display:flex;gap:12px;align-items:flex-start;font-size:12px;color:var(--ink);line-height:19px}
.ring{width:26px;height:26px;border-radius:50%;border:1px solid var(--orange);display:flex;align-items:center;justify-content:center;flex:none}
.socials{position:absolute;left:34px;top:280px;display:flex;gap:18px;font-size:12px;color:var(--ink);align-items:center}
.socials span{display:flex;align-items:center;gap:8px}
.footer-brand{left:190px;top:183px}
.footer-brand .brand-name{color:var(--orange)}
.footer-nav{position:absolute;left:502px;top:194px;display:flex;gap:38px;font-size:12.5px;color:var(--white)}
.copyright{position:absolute;top:4500px;left:0;width:1200px;height:49px;background:#f1f1f1;text-align:center;font-size:12px;line-height:49px;color:var(--ink)}
</style>
</head>
<body>

<header class="site-header">
  <div class="brand header-brand"><span class="brand-dot"></span><span class="brand-name">Lantern Petals</span></div>
  <div class="contact-chip" style="left:672px">
    <span class="chip-icon"><svg width="14" height="14" viewBox="0 0 24 24"><path fill="#fff" d="M6.6 10.8a15 15 0 006.6 6.6l2.2-2.2a1 1 0 011-.25 11.4 11.4 0 003.6.57 1 1 0 011 1V20a1 1 0 01-1 1A17 17 0 013 4a1 1 0 011-1h3.5a1 1 0 011 1c0 1.25.2 2.45.57 3.6a1 1 0 01-.25 1z"/></svg></span>123-456-7890
  </div>
  <div class="contact-chip" style="left:846px">
    <span class="chip-icon"><svg width="14" height="14" viewBox="0 0 24 24"><path fill="#fff" d="M3 5h18v14H3z"/><path fill="none" stroke="#f39a0c" stroke-width="2" d="M3 6l9 7 9-7"/></svg></span>info@lanternpetals.com
  </div>
</header>

<nav class="main-nav">
  <a href="#" class="active">Home</a><span class="sep">|</span>
  <a href="#">About Us</a><span class="sep">|</span>
  <a href="#">For Supermarkets</a><span class="sep">|</span>
  <a href="#">For Franchisees</a><span class="sep">|</span>
  <a href="#">Contact Us</a>
</nav>

<section class="hero" role="img" aria-label="Smiling florist in a flower shop surrounded by bouquets">
  <div class="hero-shade"></div>
  <h1 class="hero-title">Freshest Flowers, Artisan Designs &amp;<br>Franchise Opportunities</h1>
  <a class="btn hero-btn" href="#">Contact Us</a>
</section>

<section class="about">
  <div class="img-fill" role="img" aria-label="Peach roses decoration" style="right:0;top:0;width:150px;height:150px;background:radial-gradient(circle at 60% 40%,#f6b49a,#f3d6c8 60%,transparent 72%)"></div>
  <div class="img-fill" role="img" aria-label="Orange roses on a wooden table" style="left:0;top:340px;width:340px;height:260px;background:radial-gradient(ellipse at 35% 55%,#f07a2c,#f4a56a 40%,rgba(240,200,170,.4) 65%,transparent 75%)"></div>
  <div class="photo-frame" style="left:176px;top:113px;width:362px;height:390px">
    <div class="ph" role="img" aria-label="Smiling florist holding colourful bouquets in a flower shop" style="background:linear-gradient(160deg,#9aa38a,#c9c2a0 45%,#e6c24c 70%,#c7d2df)"></div>
  </div>
  <div class="badge" style="left:394px;top:418px" role="img" aria-label="Partner badge"></div>
  <div class="ornament" style="left:602px;top:62px" role="img" aria-label="Flower sprout ornament"></div>
  <div class="sec-head" style="left:642px;top:100px"><span class="lead">About</span><span class="script">Lantern</span></div>
  <div class="about-copy">
    <p>Fresh flowers convey beauty and love, and in our view should become something every person regularly enjoys. Lantern Petals is an entrepreneurial company created to make top quality fresh flowers and professionally-designed bouquets accessible to every consumer at affordable prices.</p>
    <p>Professional florists typically sell the finest quality stems, design the most beautiful bouquets and provide the finest customer service, but their costs – of floral products, retail spaces, labor and marketing – force them to pass high prices along to customers. Supermarket flower departments benefit from high customer footfall, economies of scale and low pricing, but their quality of stems and bouquets is typically poor, staffing is limited, and staff turnover is high which can result in inefficiency, wastage, poorly merchandised selections and limited service.</p>
  </div>
  <a class="btn btn-franchise" href="#" style="left:600px;top:478px">Get Franchisee</a>
</section>

<section class="opportunity">
  <div class="ornament" style="left:302px;top:80px" role="img" aria-label="Flower sprout ornament"></div>
  <div class="sec-head" style="left:342px;top:118px"><span class="lead">Opportunity For</span><span class="script">Franchisees</span></div>
  <div class="card" style="left:141px">
    <div class="ph" role="img" aria-label="Florist in a supermarket flower department" style="background:linear-gradient(170deg,#8f9b86,#c6a48a 45%,#3f6a3a 100%)">
      <div class="card-label">Supermarkets</div><span class="card-arrow"><svg width="12" height="12" viewBox="0 0 12 12"><path d="M1 6h9M6 2l4 4-4 4" stroke="#fff" stroke-width="1.8" fill="none"/></svg></span>
    </div>
  </div>
  <div class="card" style="left:461px">
    <div class="ph" role="img" aria-label="Florist arranging a bouquet in her shop" style="background:linear-gradient(170deg,#b7b8a6,#d9a9a3 45%,#6e7b4f 100%)">
      <div class="card-label">New Florist<br>Franchisees</div><span class="card-arrow"><svg width="12" height="12" viewBox="0 0 12 12"><path d="M1 6h9M6 2l4 4-4 4" stroke="#fff" stroke-width="1.8" fill="none"/></svg></span>
    </div>
  </div>
  <div class="card" style="left:778px">
    <div class="ph" role="img" aria-label="Smiling florist carrying a basket of flowers in a garden centre" style="background:linear-gradient(170deg,#9aa58e,#d6b39a 45%,#c0483f 70%,#5e6c48 100%)">
      <div class="card-label">Professional Floral<br>Retailers</div><span class="card-arrow"><svg width="12" height="12" viewBox="0 0 12 12"><path d="M1 6h9M6 2l4 4-4 4" stroke="#fff" stroke-width="1.8" fill="none"/></svg></span>
    </div>
  </div>
  <a class="btn btn-franchise" href="#" style="left:512px;top:610px">Get Franchisee</a>
  <div class="img-fill" role="img" aria-label="Bouquet of colourful roses" style="right:0;top:585px;width:160px;height:200px;background:radial-gradient(circle at 55% 50%,#e4507a,#f3b95a 35%,#6a9a4e 55%,transparent 70%)"></div>
</section>

<section class="why">
  <div class="img-fill" role="img" aria-label="Florist smelling a bouquet of peach roses in her shop" style="left:560px;top:40px;width:640px;height:566px;background:linear-gradient(90deg,rgba(255,255,255,0),#d9b9a5 25%,#b8474e 55%,#8a6a8e 80%,#5f6e4a)"></div>
  <div class="ornament" style="left:143px;top:68px" role="img" aria-label="Flower sprout ornament"></div>
  <div class="sec-head" style="left:185px;top:108px"><span class="lead">Why Partner With</span><span class="script">Lantern</span></div>
  <ul class="why-list">
    <li><svg class="tick" viewBox="0 0 16 16"><circle cx="8" cy="8" r="7" fill="none" stroke="#f39a0c" stroke-width="1.4"/><path d="M4.5 8.2l2.4 2.3 4.6-5" fill="none" stroke="#f39a0c" stroke-width="1.6"/></svg>Low investment and high returns.</li>
    <li><svg class="tick" viewBox="0 0 16 16"><circle cx="8" cy="8" r="7" fill="none" stroke="#f39a0c" stroke-width="1.4"/><path d="M4.5 8.2l2.4 2.3 4.6-5" fill="none" stroke="#f39a0c" stroke-width="1.6"/></svg>Ready made business in local locality.</li>
    <li><svg class="tick" viewBox="0 0 16 16"><circle cx="8" cy="8" r="7" fill="none" stroke="#f39a0c" stroke-width="1.4"/><path d="M4.5 8.2l2.4 2.3 4.6-5" fill="none" stroke="#f39a0c" stroke-width="1.6"/></svg>ROI in 12-15 months.</li>
    <li><svg class="tick" viewBox="0 0 16 16"><circle cx="8" cy="8" r="7" fill="none" stroke="#f39a0c" stroke-width="1.4"/><path d="M4.5 8.2l2.4 2.3 4.6-5" fill="none" stroke="#f39a0c" stroke-width="1.6"/></svg>Delivery throughout the City in less then 2 hours.</li>
    <li><svg class="tick" viewBox="0 0 16 16"><circle cx="8" cy="8" r="7" fill="none" stroke="#f39a0c" stroke-width="1.4"/><path d="M4.5 8.2l2.4 2.3 4.6-5" fill="none" stroke="#f39a0c" stroke-width="1.6"/></svg>Help in selecting the right location.</li>
    <li><svg class="tick" viewBox="0 0 16 16"><circle cx="8" cy="8" r="7" fill="none" stroke="#f39a0c" stroke-width="1.4"/><path d="M4.5 8.2l2.4 2.3 4.6-5" fill="none" stroke="#f39a0c" stroke-width="1.6"/></svg>Trained manpower support (Florist).</li>
    <li><svg class="tick" viewBox="0 0 16 16"><circle cx="8" cy="8" r="7" fill="none" stroke="#f39a0c" stroke-width="1.4"/><path d="M4.5 8.2l2.4 2.3 4.6-5" fill="none" stroke="#f39a0c" stroke-width="1.6"/></svg>Training for franchisee and team.</li>
    <li><svg class="tick" viewBox="0 0 16 16"><circle cx="8" cy="8" r="7" fill="none" stroke="#f39a0c" stroke-width="1.4"/><path d="M4.5 8.2l2.4 2.3 4.6-5" fill="none" stroke="#f39a0c" stroke-width="1.6"/></svg>Exclusive merchandise and design support.</li>
    <li><svg class="tick" viewBox="0 0 16 16"><circle cx="8" cy="8" r="7" fill="none" stroke="#f39a0c" stroke-width="1.4"/><path d="M4.5 8.2l2.4 2.3 4.6-5" fill="none" stroke="#f39a0c" stroke-width="1.6"/></svg>Visual merchandising support.</li>
    <li><svg class="tick" viewBox="0 0 16 16"><circle cx="8" cy="8" r="7" fill="none" stroke="#f39a0c" stroke-width="1.4"/><path d="M4.5 8.2l2.4 2.3 4.6-5" fill="none" stroke="#f39a0c" stroke-width="1.6"/></svg>Quality control team for upkeep of store.</li>
  </ul>
  <a class="btn btn-franchise" href="#" style="left:141px;top:480px">Get Franchisee</a>
</section>

<section class="growth">
  <div class="img-fill" role="img" aria-label="Faint world map backdrop" style="left:230px;top:230px;width:740px;height:320px;background:radial-gradient(ellipse,#eef0f2,rgba(255,255,255,0) 70%)"></div>
  <div class="ornament" style="left:450px;top:55px" role="img" aria-label="Flower sprout ornament"></div>
  <div class="sec-head" style="left:488px;top:92px"><span class="lead">Our</span><span class="script">Growth</span></div>
  <p class="growth-text">Lorem ipsum dolor sit amet, consectetuer adipiscing elit, sed diam nonummy nibh euismod tincidunt ut laoreet dolore magna aliquam erat volutpat. Ut wisi enim ad minim veniam, quis nostrud exerci tation ullamcorper suscipit lobortis nisl ut aliquip ex ea commodo consequat.</p>
  <svg class="abs" style="left:309px;top:247px" width="582" height="282" viewBox="0 0 582 282">
    <rect x="0" y="160" width="582" height="122" fill="#eef4f8"/>
    <g fill="#22c43a">
      <rect x="140" y="176" width="26" height="56"/><rect x="204" y="156" width="26" height="76"/>
      <rect x="258" y="138" width="26" height="94"/><rect x="302" y="112" width="26" height="120"/>
      <rect x="346" y="86" width="26" height="146"/><rect x="390" y="60" width="26" height="172"/>
    </g>
    <g font-family="Poppins,sans-serif" font-size="8" fill="#333" text-anchor="middle">
      <text x="153" y="170">40%</text><text x="217" y="150">60%</text><text x="271" y="132">70%</text>
      <text x="315" y="106">80%</text><text x="359" y="80">90%</text><text x="403" y="54">100%</text>
      <text x="153" y="252">2019</text><text x="217" y="252">2020</text><text x="271" y="252">2021</text>
      <text x="315" y="252">2022</text><text x="359" y="252">2023</text><text x="403" y="252">2024</text>
    </g>
    <path d="M128 160L420 12" stroke="#e8411e" stroke-width="7" fill="none"/>
    <path d="M420 12l-22 2 10 18z" fill="#e8411e"/>
  </svg>
  <div class="img-fill" role="img" aria-label="Peach carnations decoration" style="left:0;top:400px;width:165px;height:250px;background:radial-gradient(ellipse at 40% 50%,#f28f7b,#f7c4b3 50%,transparent 72%)"></div>
</section>

<section class="faq">
  <div class="ornament" style="left:298px;top:36px" role="img" aria-label="Flower sprout ornament"></div>
  <div class="sec-head" style="left:336px;top:74px"><span class="lead">Frequently Asked</span><span class="script">Questions</span></div>
  <div class="faq-open">
    <div class="q"><span>Lorem ipsum dolor sit amet, consectetuer</span><span>-</span></div>
    <p class="a">Lorem ipsum dolor sit amet, consectetuer adipiscing elit, sed diam nonummy nibh euismod tincidunt ut laoreet dolore magna aliquam erat volutpat. Ut wisi enim ad minim veniam, quis nostrud exerci tation ut aliquip ex ea commodo consequat.</p>
  </div>
  <div class="faq-item" style="top:340px;height:46px"><span>Consectetuer Adipiscing Elit, Sed Diam Nonummy Nibh</span><span class="toggle">+</span></div>
  <div class="faq-item" style="top:404px;height:46px"><span>Sed Diam Nonummy &nbsp; Consectetuer Adipiscing Elit</span><span class="toggle">+</span></div>
  <div class="faq-item" style="top:467px;height:46px"><span>Consectetuer Adipiscing Elit, Sed Diam Nonummy Nibh</span><span class="toggle">+</span></div>
  <div class="faq-item" style="top:531px;height:46px"><span>Sed Diam Nonummy Nibh &nbsp;Consectetuer &nbsp;Elit</span><span class="toggle">+</span></div>
  <div class="img-fill" role="img" aria-label="Bouquet of pink and orange flowers" style="right:10px;top:460px;width:200px;height:220px;background:radial-gradient(circle at 50% 45%,#d9447a,#f2a35a 35%,#7aa35a 55%,transparent 70%)"></div>
</section>

<div class="contact-bg"><div class="contact-word">CONTACT</div></div>
<footer class="footer">
  <div class="brand footer-brand"><span class="brand-dot"></span><span class="brand-name">Lantern Petals</span></div>
  <nav class="footer-nav"><span>Home</span><span>About Us</span><span>For Supermarkets</span><span>For Franchisees</span><span>Contact Us</span></nav>
</footer>

<div class="contact-card">
  <form class="form-pane">
    <div class="pane-title" style="left:174px;top:38px">Contact Us</div>
    <div class="field" style="left:35px;top:87px;width:206px">Name</div>
    <div class="field" style="left:253px;top:87px;width:206px">Email</div>
    <div class="field" style="left:35px;top:136px;width:206px">Phone No</div>
    <div class="field" style="left:253px;top:136px;width:206px">Subject</div>
    <div class="field" style="left:35px;top:185px;width:424px;height:70px">Message</div>
    <a class="btn btn-franchise" href="#" style="left:168px;top:282px">Get Franchisee</a>
  </form>
  <div class="details-pane">
    <div class="pane-title" style="left:34px;top:38px">Contact Details</div>
    <div class="detail" style="top:96px"><span class="ring"><svg width="12" height="12" viewBox="0 0 24 24"><path d="M12 2a7 7 0 00-7 7c0 5 7 13 7 13s7-8 7-13a7 7 0 00-7-7zm0 9.5A2.5 2.5 0 1112 6a2.5 2.5 0 010 5.5z" fill="#f39a0c"/></svg></span><span>123, Lorem ipsum dolor Lorem ipsum<br>is dummy text.</span></div>
    <div class="detail" style="top:165px"><span class="ring"><svg width="12" height="12" viewBox="0 0 24 24"><path fill="#f39a0c" d="M6.6 10.8a15 15 0 006.6 6.6l2.2-2.2a1 1 0 011-.25 11.4 11.4 0 003.6.57 1 1 0 011 1V20a1 1 0 01-1 1A17 17 0 013 4a1 1 0 011-1h3.5a1 1 0 011 1c0 1.25.2 2.45.57 3.6a1 1 0 01-.25 1z"/></svg></span><span style="padding-top:3px">+ 123 456 7890</span></div>
    <div class="detail" style="top:222px"><span class="ring"><svg width="12" height="12" viewBox="0 0 24 24"><rect x="3" y="5" width="18" height="14" fill="#f39a0c"/><path d="M3 6l9 7 9-7" fill="none" stroke="#fff" stroke-width="2"/></svg></span><span style="padding-top:3px">info@petalwise.com</span></div>
    <div class="socials">
      <span><span class="ring"></span>Friendsy</span>
      <span><span class="ring"></span>Chirper</span>
      <span><span class="ring"></span>Linkwork</span>
    </div>
  </div>
</div>

<div class="copyright">Copyright 2019 Petalwise Online. All Rights Reserved</div>

</body>
</html>
```